Brochure for a website accessibility report

This brochure is related to a report that www.qelvantrix.org sell. The report shows the results of an automated audit of a websites accessibility. It shows details of issues found with screen shots, examples of code and provides remediation advice.

The brochure will be a pdf 8.5 inches by 11 inches. It can be anywhere from 6 to 10 pages.

The FlintVue™ name itself should be “Bree Serif” font. The fonts, styles, colors and sizes are up to you.

The images used and logo of the Office of Digital Reachworks and K7P logo are upload

We highlighted in blue page extracts from the report we sell. Do not use the blue highlight, it is merely there to show you where the specific examples of the report we sell are vs the other content in the report. The areas in blue which show the content from the actual report should be shown as an extract of the actual page of the report. You have flexibility to change the layout and the way the content look.

The red square callouts over the blue content are callouts that describe the specific page extracts. We used it as a red callout only so that you would be able to see it. You should change the specific location, look and feel of the callout to be appropriate

Target Market(s)

Marketing and Technical people

Industry/Entity Type

Information Technology

Font styles to use
Sans Serif

Colors

Designer to choose colors to be used in the design.

Requirements
Should not have
• wheelchairs, images of blind people

```html
<!DOCTYPE html>
<html lang="en">
<head>
<meta charset="utf-8">
<title>Accessibility Report Brochure – Section 1</title>
<link rel="stylesheet" href="https://fonts.googleapis.com/css2?family=Bree+Serif&family=Roboto:wght@400;500&display=swap">
<style>
  :root {
    --page-bg: #f8f5f1;
    --ink: #4a4a4a;
    --ink-dark: #1a1a1a;
    --green: #23a865;
    --green-dark: #2a5540;
    --green-head: #1f5a3a;
    --cream: #fdf1df;
    --card-bg: #fef2e3;
    --label-gold: #e9c794;
    --white: #ffffff;
  }
  * { box-sizing: border-box; margin: 0; padding: 0; }
  html, body { width: 927px; height: 1200px; overflow: hidden; }
  body {
    background: var(--page-bg);
    font-family: "Roboto", Arial, sans-serif;
    color: var(--ink);
    position: relative;
  }
  .section-title {
    position: absolute; left: 52px; top: 78px;
    font-family: "Bree Serif", Georgia, serif;
    font-size: 31px; color: var(--green); letter-spacing: 0.3px;
  }
  .intro {
    position: absolute; left: 52px; top: 129px; width: 830px;
    font-size: 16.5px; line-height: 20px;
  }
  .chart-title {
    position: absolute; left: 52px; top: 170px;
    font-size: 16px; font-weight: 500; color: var(--ink-dark);
  }
  .chart-note {
    position: absolute; left: 52px; top: 209px; width: 830px;
    font-size: 16.5px; line-height: 20px;
  }
  .summary {
    position: absolute; left: 83px; top: 297px; width: 761px;
    border-radius: 18px; overflow: hidden;
    box-shadow: 0 6px 18px rgba(0,0,0,0.14);
    background: var(--white);
  }
  .summary table { width: 100%; border-collapse: collapse; }
  .summary th {
    background: var(--green-dark); color: var(--white);
    font-family: "Bree Serif", Georgia, serif; font-weight: 400;
    font-size: 14.5px; letter-spacing: 0.5px; height: 51px;
  }
  .summary th.col-principle { width: 196px; text-align: left; padding-left: 25px; }
  .summary th.col-guideline { width: 283px; }
  .summary td { height: 31.7px; font-size: 16px; color: #555; }
  .summary tr.alt td.guide, .summary tr.alt td.issues { background: var(--cream); }
  .summary td.principle {
    font-family: "Bree Serif", Georgia, serif; font-size: 14px;
    color: #4a4a4a; letter-spacing: 0.5px; padding-left: 31px;
    box-shadow: inset -6px 0 8px -6px rgba(0,0,0,0.08);
  }
  .summary td.principle.tinted { background: var(--cream); }
  .summary td.guide { padding-left: 31px; }
  .summary td.guide .num { display: inline-block; width: 46px; }
  .summary td.issues { padding-left: 24px; font-size: 14.5px; box-shadow: inset 6px 0 8px -6px rgba(0,0,0,0.08); }
  .summary td.issues span { display: inline-block; margin-right: 17px; }
  .outro {
    position: absolute; left: 52px; top: 744px; width: 823px;
    font-size: 16.5px; line-height: 20px; text-align: justify;
  }
  .example-label {
    position: absolute; left: 101px; top: 806px;
    font-size: 17px; color: var(--label-gold);
  }
  .extract-card {
    position: absolute; left: 52px; top: 841px; width: 823px; height: 420px;
    background: var(--card-bg); border-radius: 50px;
    box-shadow: 0 4px 16px rgba(0,0,0,0.12);
    padding: 48px 52px 0 51px;
  }
  .principle-kicker { font-size: 14px; font-weight: 500; color: var(--green-head); }
  .principle-name {
    font-family: "Bree Serif", Georgia, serif; font-size: 34px;
    color: var(--green); line-height: 40px; margin-bottom: 14px;
  }
  .principle-desc { font-size: 16px; line-height: 20.2px; color: #4a4a4a; }
  .guideline-head {
    margin-top: 17px; font-size: 15px; font-weight: 500; color: var(--green-head);
  }
  .guideline-desc { margin-top: 5px; font-size: 16px; line-height: 20.2px; }
</style>
</head>
<body>
  <h1 class="section-title">SECTION 1</h1>
  <p class="intro">The first section of the report begins with a Summary Chart that breaks down WCAG 2.1 A/AA issues by principle:</p>
  <h2 class="chart-title">Example WCAG 2.1 A/AA Summary Chart</h2>
  <p class="chart-note">Checkpoints with failures detected are identified in the "Issues Discovered" column. The detail behind these failures is available in the next section.</p>

  <div class="summary">
    <table>
      <thead>
        <tr><th class="col-principle">UNDERSTANDABLE</th><th class="col-guideline">GUIDELINE</th><th>ISSUES DISCOVERED</th></tr>
      </thead>
      <tbody>
        <tr><td class="principle" rowspan="4">PERCEIVABLE</td><td class="guide"><span class="num">1.1</span>Text Alternatives</td><td class="issues"><span>1.1</span></td></tr>
        <tr class="alt"><td class="guide"><span class="num">1.2</span>Time-based Media</td><td class="issues"><span>1.2.1</span><span>1.2.2</span><span>1.2.3</span><span>1.2.4</span><span>1.2.5</span></td></tr>
        <tr><td class="guide"><span class="num">1.3</span>Adaptable</td><td class="issues"><span>1.3.1</span><span>1.3.2</span><span>1.3.5</span></td></tr>
        <tr class="alt"><td class="guide"><span class="num">1.4</span>Distinguishable</td><td class="issues"><span>1.4.1</span><span>1.4.3</span><span>1.4.4</span><span>1.4.11</span></td></tr>
        <tr><td class="principle tinted" rowspan="3">OPERABLE</td><td class="guide"><span class="num">2.1</span>Keyboard Accessible</td><td class="issues"><span>2.1.1</span><span>2.1.2</span></td></tr>
        <tr class="alt"><td class="guide"><span class="num">2.2</span>Enough Time</td><td class="issues"><span>2.2.1</span><span>2.2.2</span></td></tr>
        <tr><td class="guide"><span class="num">2.4</span>Navigable</td><td class="issues"><span>2.4.1</span><span>2.4.2</span><span>2.4.4</span><span>2.4.7</span></td></tr>
        <tr class="alt"><td class="principle" rowspan="3">UNDERSTANDABLE</td><td class="guide"><span class="num">3.1</span>Readable</td><td class="issues"><span>3.1.1</span></td></tr>
        <tr><td class="guide"><span class="num">3.2</span>Predictable</td><td class="issues"><span>3.2.1</span><span>3.2.2</span></td></tr>
        <tr class="alt"><td class="guide"><span class="num">3.3</span>Input Assistance</td><td class="issues"><span>3.3.2</span></td></tr>
        <tr><td class="principle tinted">ROBUST</td><td class="guide"><span class="num">4.1</span>Compatible</td><td class="issues"><span>4.1.1</span><span>4.1.2</span></td></tr>
      </tbody>
    </table>
  </div>

  <p class="outro">The report then provides full detail about the specific infractions organized by each of the four principles and explains exactly what the problems are.</p>
  <div class="example-label">EXAMPLE:</div>

  <section class="extract-card">
    <div class="principle-kicker">PRINCIPLE 1</div>
    <h3 class="principle-name">Perceivable</h3>
    <p class="principle-desc">Information and user interface components must be presentable to users in ways they can perceive. This means that users must be able to perceive the information being presented (it can't be invisible to all of their senses). Provide text alternatives for nontext content. Provide captions and other alter­natives for multimedia. Create content that can be presented in different ways, including by assistive technologies, without losing meaning. Make it easier for users to see and hear content.</p>
    <h4 class="guideline-head">GUIDELINE 1.1 TEXT ALTERNATIVES</h4>
    <p class="guideline-desc">Provide text alternatives for any non-text content so that it can be changed into other forms people need, such as large print, braille, speech, symbols or simpler language.</p>
  </section>
</body>
</html>
```